Website Design - TallyPorchHelpers.net

PLEASE CHECK WORD DOCUMENT ATTACHED FOR WEBSITE FLOW.

Target Market(s)

REAL ESTATE AGENTS ARE THE TARGET MARKET

Industry/Entity Type

Real Estate

Coding

Coded - Design and coding required

Number of Pages Required

4 page

Colors

Designer to choose colors to be used in the design.

Requirements
Must have
• WE LIKE RED LOGO ATTACHED
Nice to have
• PLEASE CHECK WORD DOCUMENT ATTACHED FOR WEBSITE FLOW.
Should not have

```html
<!DOCTYPE html>
<html lang="en">
<head>
<meta charset="utf-8">
<title>TallyPorchHelpers.net</title>
<link rel="stylesheet" href="https://fonts.googleapis.com/css2?family=Lato:wght@400;700;900&family=Oswald:wght@500&display=swap">
<style>
:root{
  --red:#e3101e;
  --red-dark:#b80f1a;
  --navy:#2c2488;
  --navy-dark:#231c73;
  --ink:#333;
  --muted:#666;
  --grey-bg:#efefef;
  --dark-band:#333333;
  --footer:#2b2b2b;
  --line:#d7d7d7;
}
*{box-sizing:border-box;margin:0;padding:0}
html,body{width:1200px;height:4852px;overflow:hidden}
body{position:relative;font-family:"Lato",Arial,sans-serif;color:var(--ink);background:#fff}
.abs{position:absolute}
.section-title{position:absolute;left:0;width:1200px;text-align:center;font-weight:700;font-size:30px;letter-spacing:.5px;text-transform:uppercase}

/* header */
.site-header{top:0;left:0;width:1200px;height:120px;background:#fff}
.brand{left:76px;top:34px;display:flex;align-items:center;gap:10px;font-weight:900;font-size:24px;color:var(--red)}
.brand-dot{width:30px;height:30px;background:var(--red);border-radius:50%}
.signup{left:566px;top:44px;display:flex}
.signup input{width:240px;height:40px;border:1px solid var(--line);border-radius:20px 0 0 20px;padding:0 16px;font:14px "Lato",sans-serif}
.signup button{height:40px;width:102px;margin-left:-10px;background:var(--navy);color:#fff;border:0;border-radius:20px;font:700 14px "Lato",sans-serif}
.call{left:928px;top:34px;display:flex;align-items:center;gap:14px}
.call-icon{width:40px;height:40px;border-radius:50%;background:var(--red);display:flex;align-items:center;justify-content:center}
.call small{display:block;font-size:13px;font-weight:700;color:var(--red)}
.call strong{display:block;font-size:19px;color:var(--red)}

.main-nav{top:120px;left:0;width:1200px;height:58px;background:var(--navy);display:flex;align-items:center;padding-left:76px;gap:38px}
.main-nav a{color:#fff;text-decoration:none;font-size:14px;font-weight:700}

/* hero */
.hero{top:178px;left:0;width:1200px;height:566px;background:linear-gradient(180deg,#8a95a5 0%,#4e5a6c 45%,#3c4a3a 100%)}
.hero h1{position:absolute;top:135px;left:130px;width:940px;text-align:center;color:#fff;font-size:33px;line-height:44px;font-weight:700}
.hero-arrow{position:absolute;top:170px;color:#fff;font-size:34px}
.hero-cta{position:absolute;top:427px;width:330px;height:123px;background:linear-gradient(180deg,var(--red),var(--red-dark));border-radius:6px;color:#fff;text-align:center;font-weight:700;font-size:16px;padding-top:30px}
.hero-cta svg{display:block;margin:0 auto 16px}

/* how it works */
.step-circle{position:absolute;top:862px;width:116px;height:116px;border-radius:50%;background:var(--navy);color:#fff;font-size:44px;display:flex;align-items:center;justify-content:center}
.step-text{position:absolute;top:998px;width:250px;text-align:center;font-size:14px;line-height:21px}
.step-arrow{position:absolute;top:910px}

/* packages */
.packages{top:1148px;left:0;width:1200px;height:598px;background:var(--grey-bg)}
.pkg{position:absolute;top:123px;width:199px;height:452px;background:#fff;border:1px solid var(--line);border-radius:4px;text-align:center;padding-top:14px;font-size:13px;line-height:18px}
.pkg .badge{width:96px;height:96px;margin:0 auto 18px;border-radius:50%;background:var(--navy);color:#fff;display:flex;flex-direction:column;align-items:center;justify-content:center;font-family:"Oswald",sans-serif}
.pkg .badge span{font-size:13px}
.pkg .badge b{font-size:21px;font-weight:500}
.pkg p{margin:0 18px 16px}
.pkg .buy{display:inline-block;width:130px;height:32px;line-height:32px;border-radius:16px;background:var(--red);color:#fff;font-weight:700;font-size:13px;margin:4px 0 12px}
.pkg .fine{font-size:9px;line-height:12px;margin:0 12px;font-weight:700}
.pkg.featured{background:linear-gradient(180deg,var(--red) 0%,#8a1a4e 60%,var(--navy) 100%);color:#fff;border-color:var(--red)}
.pkg.featured .badge{background:#fff;color:var(--red)}
.pkg.featured .buy{background:#fff;color:var(--red)}
.custom-tag{position:absolute;top:76px;left:2px;right:2px;background:var(--red);color:#fff;font-size:9px;font-weight:700;line-height:16px}

/* services */
.services{top:1756px;left:0;width:1200px;height:388px;background:var(--dark-band);color:#fff}
.services h2{position:absolute;top:46px;width:1200px;text-align:center;font-size:28px;line-height:38px;font-weight:700}
.svc{position:absolute;top:150px;width:250px;text-align:center;font-size:13px;line-height:19px}
.svc svg{display:block;margin:0 auto 10px}
.svc h3{font-size:19px;margin-bottom:8px}

/* service area */
.area-box{position:absolute;top:2264px;height:233px;border:1px solid var(--line);text-align:center;padding-top:18px;box-shadow:0 2px 6px rgba(0,0,0,.08)}
.area-box h3{font-size:20px;margin:10px 0 12px}
.area-box p{font-size:13px;line-height:22px;color:var(--muted);margin:0 40px}

/* map */
.locate{top:2561px;left:0;width:446px;height:569px;background:#fff}
.locate h2{position:absolute;top:68px;left:76px;font-size:28px;line-height:32px;font-weight:900;text-transform:uppercase}
.locate .field{position:absolute;top:212px;left:76px;width:330px;height:36px;border:1px solid var(--line);display:flex;align-items:center;justify-content:space-between;padding:0 12px;font-size:12px}
.map{top:2561px;left:446px;width:754px;height:569px;background:linear-gradient(135deg,#d9e4c6 0%,#e9e2cf 50%,#a9cbe6 100%)}

/* faq */
.faq-item{position:absolute;left:76px;width:1048px;border:1px solid var(--line);border-radius:4px;font-size:19px;padding:0 30px;display:flex;align-items:center;justify-content:space-between;height:62px}
.faq-open{position:absolute;left:76px;top:3260px;width:1048px;border:1px solid var(--line);border-radius:4px}
.faq-open .q{height:62px;padding:0 30px;display:flex;align-items:center;justify-content:space-between;font-size:19px}
.faq-open .a{background:#eee;padding:14px 22px;font-size:15px;line-height:22px;color:var(--muted);height:112px}

/* testimonial */
.testimonial{top:3735px;left:0;width:1200px;height:453px;background:var(--red)}
.testimonial .card{position:absolute;top:107px;left:204px;width:792px;height:281px;background:#fff;text-align:center;padding-top:50px}
.avatar{width:76px;height:76px;margin:0 auto 20px;border-radius:50%;background:linear-gradient(180deg,#c9b19c,#7d6a5a)}
.testimonial q{display:block;font-size:15px;line-height:21px;color:var(--muted);margin:0 140px 4px}
.testimonial .name{font-size:19px}
.testimonial .role{font-size:12px;color:var(--muted);margin-top:6px}
.dots{position:absolute;top:416px;width:1200px;display:flex;justify-content:center;gap:10px}
.dots i{width:10px;height:10px;border-radius:50%;background:#fff}

/* contact */
.form-field{position:absolute;height:38px;background:#eeeeee;font-size:12px;font-weight:700;padding:12px 20px}
.submit{position:absolute;top:4550px;left:529px;width:142px;height:36px;border-radius:18px;background:var(--navy);color:#fff;border:0;font:700 13px "Lato",sans-serif}
.newsletter-tab{top:4262px;left:1151px;width:49px;height:324px;background:var(--navy);border:3px solid var(--red);border-right:0;border-radius:10px 0 0 10px;color:#fff;font-weight:700;font-size:17px;writing-mode:vertical-rl;transform:rotate(180deg);display:flex;align-items:center;justify-content:center}

/* footer */
.site-footer{top:4657px;left:0;width:1200px;height:195px;background:var(--footer);color:#fff}
.site-footer .brand{top:34px;left:80px;color:#fff;font-size:22px}
.site-footer .brand-dot{background:var(--red)}
.foot-about{position:absolute;top:118px;left:80px;width:400px;font-size:12px;line-height:17px;font-weight:700}
.foot-nav{position:absolute;top:56px;right:76px;display:flex;gap:40px;font-size:13px;font-weight:700}
.copy{position:absolute;top:86px;right:76px;font-size:12px;color:#ccc}
.socials{position:absolute;top:120px;right:76px;display:flex;gap:16px}
.socials i{width:20px;height:20px;border-radius:50%;background:#fff}
</style>
</head>
<body>

<header class="site-header abs">
  <div class="brand abs"><span class="brand-dot"></span>TallyPorch</div>
  <form class="signup abs"><input placeholder="Enter Email Address"><button type="button">SIGN UP</button></form>
  <div class="call abs">
    <div class="call-icon"><svg width="20" height="20" viewBox="0 0 24 24"><path fill="#fff" d="M6.6 10.8a15 15 0 0 0 6.6 6.6l2.2-2.2c.3-.3.7-.4 1-.2 1.1.4 2.3.6 3.6.6.6 0 1 .4 1 1V20c0 .6-.4 1-1 1A17 17 0 0 1 3 4c0-.6.4-1 1-1h3.5c.6 0 1 .4 1 1 0 1.3.2 2.5.6 3.6.1.3 0 .7-.2 1z"/></svg></div>
    <div><small>CALL OR TEXT US</small><strong>1-555-014-2290</strong></div>
  </div>
</header>

<nav class="main-nav abs">
  <a href="#">HOW IT WORKS</a><a href="#">SERVICE AREA</a><a href="#">PRICING</a><a href="#">ABOUT US</a><a href="#">FAQ</a>
</nav>

<section class="hero abs" role="img" aria-label="Photo of a two-storey suburban house with a front porch at dusk">
  <span class="hero-arrow" style="left:62px">&#10094;</span>
  <span class="hero-arrow" style="left:1116px">&#10095;</span>
  <h1>Helping agents save time and money. We place signs and boost foot traffic to your&nbsp; open houses using proven marketing techniques.</h1>
  <div class="hero-cta" style="left:76px"><svg width="26" height="26" viewBox="0 0 24 24"><circle cx="12" cy="7" r="5" fill="#fff"/><path d="M2 23c0-6 4-9 10-9s10 3 10 9z" fill="#fff"/></svg>I'M A FULL ON BROKERAGE</div>
  <div class="hero-cta" style="left:435px"><svg width="34" height="26" viewBox="0 0 34 24"><circle cx="17" cy="6" r="5" fill="#fff"/><circle cx="6" cy="9" r="4" fill="#fff"/><circle cx="28" cy="9" r="4" fill="#fff"/><path d="M7 24c0-6 4-9 10-9s10 3 10 9zM0 22c0-5 3-7 6-7s4 1 4 1l-2 6zM34 22c0-5-3-7-6-7s-4 1-4 1l2 6z" fill="#fff"/></svg>I'M AN IND. BROKER WITH A TEAM</div>
  <div class="hero-cta" style="left:794px"><svg width="26" height="26" viewBox="0 0 24 24"><rect x="1" y="1" width="22" height="22" rx="3" fill="#fff"/><path d="M7 17l1-4 7-7 3 3-7 7z" fill="#c0101c"/></svg>I NEED SIGN PLACEMENT ASAP</div>
</section>

<h2 class="section-title" style="top:790px;color:var(--navy)">How It Works</h2>
<div class="step-circle" style="left:181px">01</div>
<div class="step-circle" style="left:542px">02</div>
<div class="step-circle" style="left:902px">02</div>
<svg class="step-arrow" style="left:360px" width="120" height="20" viewBox="0 0 120 20"><path d="M0 10h114M104 2l12 8-12 8" stroke="#999" stroke-width="2" fill="none"/></svg>
<svg class="step-arrow" style="left:720px" width="120" height="20" viewBox="0 0 120 20"><path d="M0 10h114M104 2l12 8-12 8" stroke="#999" stroke-width="2" fill="none"/></svg>
<p class="step-text" style="left:114px">We boost Foot Traffic To Your Open House Using Proven Marketing Channels Social Feed Ads, SMS Notifications, Voice Broadcasts and Email Notifications</p>
<p class="step-text" style="left:475px">We Place Open House Signs Strategically In The Surrounding Area</p>
<p class="step-text" style="left:835px">We Pick Up The Signs Once Your Open House Ends</p>

<section class="packages abs">
  <h2 class="section-title" style="top:56px">Packages</h2>
  <div class="pkg" style="left:78px"><div class="badge"><span>$49</span><b>5 SIGNS</b></div><p>Place signs strategically in best areas according to where the open house is located</p><p>Pick Up the signs after the open house</p><p>Store custom signs for you if needed</p><span class="buy">BUY NOW</span><p class="fine">Sign Up For A Subscription To Receive Our Marketing Components For FREE</p></div>
  <div class="pkg" style="left:289px"><div class="badge"><span>$59</span><b>10 SIGNS</b></div><p>Place signs strategically in best areas according to where the open house is located</p><p>Pick Up the signs after the open house</p><p>Store custom signs for you if needed</p><span class="buy">BUY NOW</span><p class="fine">Sign Up For A Subscription To Receive Our Marketing Components For FREE</p></div>
  <div class="pkg featured" style="left:500px"><div class="badge"><span>$69</span><b>15 SIGNS</b></div><p>Place signs strategically in best areas according to where the open house is located</p><p>Pick Up the signs after the open house</p><p>Store custom signs for you if needed</p><span class="buy">BUY NOW</span><p class="fine">Sign Up For A Subscription To Receive Our Marketing Components For FREE</p></div>
  <div class="pkg" style="left:711px"><div class="badge"><span>$79</span><b>20 SIGNS</b></div><p>Place signs strategically in best areas according to where the open house is located</p><p>Pick Up the signs after the open house</p><p>Store custom signs for you if needed</p><span class="buy">BUY NOW</span><p class="fine">Sign Up For A Subscription To Receive Our Marketing Components For FREE</p></div>
  <div class="pkg" style="left:922px"><div class="badge"><b>25+ SIGNS</b></div><span class="custom-tag">Click Buy Now To Create Custom Pkg</span><p>Place signs strategically in best areas according to where the open house is located</p><p>Pick Up the signs after the open house</p><p>Store custom signs for you if needed</p><span class="buy">BUY NOW</span><p class="fine">Sign Up For A Subscription To Receive Our Marketing Components For FREE</p></div>
</section>

<section class="services abs">
  <h2>SERVICES-SIGN UP FOR A SUBSCRIPTION AND GET<br>THESE MARKETING SERVICES FOR FREE</h2>
  <div class="svc" style="left:76px"><svg width="40" height="44" viewBox="0 0 40 44"><rect x="8" y="2" width="22" height="40" rx="3" fill="none" stroke="#fff" stroke-width="3"/><rect x="16" y="8" width="22" height="14" rx="2" fill="#fff"/></svg><h3>SMS</h3>Send sms blast to your neighborhood informing them your home is for sale and if they know anyone looking to send them over</div>
  <div class="svc" style="left:338px"><svg width="48" height="44" viewBox="0 0 48 36"><rect x="1" y="1" width="46" height="34" fill="#fff"/><path d="M2 3l22 17L46 3" stroke="#333" stroke-width="3" fill="none"/></svg><h3>EMAIL</h3>Send email blast to your neighborhood informing them your home is for sale and if they know anyone looking to send them over</div>
  <div class="svc" style="left:610px"><svg width="44" height="44" viewBox="0 0 24 24"><rect x="2" y="3" width="20" height="18" rx="2" fill="none" stroke="#fff" stroke-width="2"/><rect x="5" y="6" width="14" height="5" fill="#fff"/><path d="M5 14h14M5 17h9" stroke="#fff" stroke-width="2"/></svg><h3>FEED AD</h3>Newsfeed ads to people in your open house area</div>
  <div class="svc" style="left:874px"><svg width="44" height="44" viewBox="0 0 24 24"><path fill="#fff" d="M12 2l11 10h-3v10h-6v-7h-4v7H4V12H1z"/></svg><h3>VB</h3>Send VB blast to your neighborhood informing them your home is for sale and if they know anyone looking to send them over</div>
</section>

<h2 class="section-title" style="top:2194px">Service Area</h2>
<div class="area-box" style="left:62px;width:326px"><svg width="80" height="80" viewBox="0 0 80 80"><path d="M10 14h60M20 14v54M20 26h40v22H20" stroke="var(--red)" stroke-width="4" fill="none"/><path d="M10 68h24" stroke="var(--red)" stroke-width="4"/></svg><h3>Lorium ipsum</h3><p>Eu in ultricies et molestie viverra quisque leo vitae pede vitae curabitur.</p></div>
<div class="area-box" style="left:433px;width:333px"><svg width="80" height="80" viewBox="0 0 80 80"><path d="M12 68V50h10v18M30 68V40h10v28M48 68V30h10v38M10 40l22-16 14 8 24-20" stroke="var(--red)" stroke-width="4" fill="none"/><circle cx="58" cy="56" r="12" fill="none" stroke="var(--red)" stroke-width="3"/></svg><h3>Dolar Amit</h3><p>Eu in ultricies et molestie viverra quisque leo vitae pede vitae curabitur.</p></div>
<div class="area-box" style="left:808px;width:327px"><svg width="80" height="80" viewBox="0 0 80 80"><circle cx="30" cy="24" r="12" fill="none" stroke="var(--red)" stroke-width="3"/><circle cx="50" cy="44" r="8" fill="none" stroke="var(--red)" stroke-width="3"/><path d="M32 68c0-10 8-14 18-14s18 4 18 14z" fill="none" stroke="var(--red)" stroke-width="3"/></svg><h3>Nemo enim</h3><p>Eu in ultricies et molestie viverra quisque leo vitae pede vitae curabitur.</p></div>

<section class="locate abs">
  <h2>Enter your open<br>house address to see<br>if we service it.</h2>
  <div class="field"><span>Enter your location</span><svg width="12" height="16" viewBox="0 0 24 32"><path d="M12 0a12 12 0 0 0-12 12c0 9 12 20 12 20s12-11 12-20A12 12 0 0 0 12 0zm0 17a5 5 0 1 1 0-10 5 5 0 0 1 0 10z" fill="#333"/></svg></div>
</section>
<div class="map abs" role="img" aria-label="Road map of the coastal service region with the covered area outlined"></div>

<h2 class="section-title" style="top:3176px">FAQ</h2>
<div class="faq-open"><div class="q">LOREM IPSUM IS SIMPLY DUMMY TEXT OF THE PRINTING?<span>&#8964;</span></div><div class="a">Lorem ipsum dolor sit amet, consectetur adipiscing elit, sed do eiusmod tempor incididunt ut labore et dolore magna aliqua. Ut enim ad minim veniam, quis nostrud exercitation ullamco laboris nisi ut aliquip ex ea commodo consequat. Duis aute irure dolor in reprehenderit in voluptate velit esse cillum dolore eu fugiat nulla pariatur.</div></div>
<div class="faq-item" style="top:3456px">LOREM IPSUM IS SIMPLY DUMMY TEXT OF THE PRINTING?<span>&#8250;</span></div>
<div class="faq-item" style="top:3531px">LOREM IPSUM IS SIMPLY DUMMY TEXT OF THE PRINTING?<span>&#8250;</span></div>
<div class="faq-item" style="top:3606px">LOREM IPSUM IS SIMPLY DUMMY TEXT OF THE PRINTING?<span>&#8250;</span></div>

<section class="testimonial abs">
  <h2 class="section-title" style="top:34px;color:#fff">Testimonial</h2>
  <div class="card">
    <div class="avatar" role="img" aria-label="Client portrait"></div>
    <q>Suspendisse et quis. Ante est feugiat. Urna odio tristique. Amet vel semper. Turpis hac in mattis quam placerat tincidunt magna aliquet</q>
    <div class="name">Alina Voss</div>
    <div class="role">Listing Agent, Oakridge</div>
  </div>
  <div class="dots"><i></i><i></i><i></i><i></i></div>
</section>

<h2 class="section-title" style="top:4246px">Contact Us Right Now</h2>
<div class="form-field" style="top:4320px;left:252px;width:340px">NAME</div>
<div class="form-field" style="top:4320px;left:612px;width:332px">EMAIL</div>
<div class="form-field" style="top:4380px;left:252px;width:692px">CELL PHONE</div>
<div class="form-field" style="top:4440px;left:252px;width:692px;height:88px">MESSAGE</div>
<button class="submit" type="button">SUBMIT</button>

<div class="newsletter-tab abs">Subscribe Our Newsletter</div>

<footer class="site-footer abs">
  <div class="brand abs"><span class="brand-dot"></span>TallyPorch</div>
  <p class="foot-about">Owned and operated by a highly experienced and skilled Promoter. An Expert Marketer and a Savvy Realtor we help agents leverage their time and skills to increase production at an affordable price with impeccable support!</p>
  <div class="foot-nav"><span>HOW IT WORKS</span><span>SERVICE AREA</span><span>PRICING</span><span>ABOUT US</span><span>FAQ</span></div>
  <div class="copy">Copyright © 2018. Company Name. All Right Reserved</div>
  <div class="socials"><i></i><i></i><i></i><i></i><i></i></div>
</footer>

</body>
</html>
```